We are a recruitment company based in Norwich/Cambridge England.
I have included our company logo which we want to remain the same.

What we are looking for is a new creative Business card which will really stand out!!

Contact Information for Business Card

Harriet Dunmore
email: Harriet@plavex.co.uk
Address: Brackwell House
Fenmoor Enterprise Park
Partridge Way
Norwich
QB9 3KX
Tel:01632 960418

```html
<!DOCTYPE html>
<html lang="en">
<head>
<meta charset="utf-8">
<title>Plavex Business Card</title>
<link href="https://fonts.googleapis.com/css2?family=Montserrat:wght@700&family=Roboto:wght@400;500&display=swap" rel="stylesheet">
<style>
  :root {
    --backdrop: #2b2b2b;
    --paper: #f1f1f1;
    --green: #8cc63f;
    --grey: #8e898f;
    --logo-grey: #7e797f;
    --white: #ffffff;
  }
  * { margin: 0; padding: 0; box-sizing: border-box; }
  html, body { width: 1200px; height: 960px; overflow: hidden; }
  body { background: var(--backdrop); position: relative; font-family: "Roboto", Arial, sans-serif; }

  .card { position: absolute; width: 600px; height: 342px; overflow: hidden; }
  .card-front { left: 322px; top: 108px; background: var(--paper); }
  .card-back { left: 320px; top: 493px; background: var(--grey); }

  .front-shape { position: absolute; inset: 0; }

  .brand { position: absolute; left: 40px; top: 146px; display: flex; align-items: center; gap: 12px; }
  .brand-dot { width: 50px; height: 50px; border-radius: 50%; background: var(--green); }
  .brand-name { font-family: "Roboto", Arial, sans-serif; font-weight: 500; font-size: 40px; color: var(--logo-grey); letter-spacing: -0.5px; }

  .details { position: absolute; left: 362px; top: 0; width: 238px; height: 100%; color: var(--white); }
  .row { position: absolute; left: 0; display: flex; align-items: center; gap: 14px; white-space: nowrap; }
  .icon { width: 22px; height: 22px; border-radius: 50%; background: var(--white); flex: none; display: flex; align-items: center; justify-content: center; }
  .icon svg { width: 14px; height: 14px; fill: var(--green); }

  .person { top: 62px; }
  .person-name { font-family: "Montserrat", Arial, sans-serif; font-weight: 700; font-size: 17px; line-height: 22px; }
  .person-role { font-family: "Montserrat", Arial, sans-serif; font-weight: 700; font-size: 14px; line-height: 17px; }

  .divider { position: absolute; left: 0; right: 0; top: 119px; height: 2px; background: var(--white); }

  .contact { font-size: 14px; line-height: 18px; }
  .address { top: 142px; }
  .phone { top: 194px; }
  .web { top: 245px; }

  .back-name { position: absolute; left: 0; right: 0; top: 120px; text-align: center; font-weight: 500; font-size: 64px; color: var(--white); }
  .back-url { position: absolute; left: 0; right: 0; top: 299px; text-align: center; font-size: 14px; letter-spacing: 5px; color: var(--white); }
</style>
</head>
<body>

<section class="card card-front">
  <svg class="front-shape" viewBox="0 0 600 342" width="600" height="342" aria-hidden="true">
    <path d="M246,0 Q370,171 249,342 L600,342 L600,0 Z" fill="var(--grey)"/>
    <path d="M263,0 Q384,171 266,342 L600,342 L600,0 Z" fill="var(--green)"/>
    <path d="M263,0 Q384,171 266,342" fill="none" stroke="var(--white)" stroke-width="2"/>
  </svg>

  <div class="brand">
    <span class="brand-dot"></span>
    <span class="brand-name">Plavex</span>
  </div>

  <div class="details">
    <div class="row person">
      <span class="icon"><svg viewBox="0 0 16 16"><circle cx="8" cy="5" r="3.2"/><path d="M2 15c0-3.6 2.7-5.6 6-5.6s6 2 6 5.6z"/></svg></span>
      <div>
        <div class="person-name">HARRIET DUNMORE</div>
        <div class="person-role">CEO/FOUNDER</div>
      </div>
    </div>

    <div class="divider"></div>

    <div class="row contact address">
      <span class="icon"><svg viewBox="0 0 16 16"><path d="M8 1a5 5 0 0 0-5 5c0 3.6 5 9 5 9s5-5.4 5-9a5 5 0 0 0-5-5zm0 7a2 2 0 1 1 0-4 2 2 0 0 1 0 4z"/></svg></span>
      <div>Brackwell House, QB9 3KX<br>Fenmoor Enterprise Park</div>
    </div>

    <div class="row contact phone">
      <span class="icon"><svg viewBox="0 0 16 16"><path d="M4.2 1.5l2 2.8c.3.4.2 1-.1 1.3l-1 1c.8 1.7 2.1 3 3.8 3.8l1-1c.3-.3.9-.4 1.3-.1l2.8 2c.4.3.5.9.1 1.3l-1.2 1.3c-.6.6-1.5.8-2.3.5C6.5 13 3 9.5 1.6 5.4c-.3-.8-.1-1.7.5-2.3l1.3-1.2c.3-.4.9-.3.8-.4z"/></svg></span>
      <div>01632 960418<br>01632 960772</div>
    </div>

    <div class="row contact web">
      <span class="icon"><svg viewBox="0 0 16 16"><circle cx="8" cy="8" r="6.5" fill="none" stroke="var(--green)" stroke-width="1.6"/><path d="M2 8h12M8 1.5c-2.5 3.5-2.5 9.5 0 13M8 1.5c2.5 3.5 2.5 9.5 0 13" fill="none" stroke="var(--green)" stroke-width="1.2"/></svg></span>
      <div>Harriet@plavex.co.uk<br>www.plavex.co.uk</div>
    </div>
  </div>
</section>

<section class="card card-back">
  <div class="back-name">Plavex</div>
  <div class="back-url">www.plavex.co.uk</div>
</section>

</body>
</html>
```